BOLD & MINIMALIST DESIGN NEEDED

We want a very bold but minimalistic business card design that is impactful and utilizes both sides of the business card. Our current logo is included for your use.

We want bold fonts and good use of negative space. We don't want the logo to overpower the design.

Target Market(s)

Professionals who are building new commercial buildings.

Industry/Entity Type

Construction

Contact Information for Business Card

Name, Title, email, office phone, cell phone, website

Font styles to use
Serif
Sans Serif

Requirements
Must have
• Bold design!

```html
<!DOCTYPE html>
<html lang="en">
<head>
<meta charset="utf-8">
<title>Ridgeline Design + Build — Business Card</title>
<link rel="stylesheet" href="https://fonts.googleapis.com/css2?family=Montserrat:wght@400;500;800&display=swap">
<style>
  :root {
    --stage: #3a3a3c;
    --lime: #86c540;
    --lime-light: #a6d86f;
    --lime-deep: #3f7a2c;
    --ink: #0b0b0c;
    --paper: #ffffff;
  }
  * { margin: 0; padding: 0; box-sizing: border-box; }
  html, body { width: 1200px; height: 689px; overflow: hidden; }
  body {
    background: var(--stage);
    font-family: "Montserrat", sans-serif;
    position: relative;
  }
  .card {
    position: absolute;
    width: 560px;
    height: 320px;
    border-radius: 22px;
    overflow: hidden;
  }
  /* Front side */
  .card-front {
    left: 30px; top: 80px;
    background: linear-gradient(120deg, var(--lime-light) 0%, var(--lime) 45%, var(--lime) 100%);
    display: flex; align-items: center; justify-content: center;
  }
  .front-brand {
    text-align: center;
    color: var(--lime-deep);
    font-weight: 800;
    text-transform: uppercase;
    line-height: 1.1;
  }
  .front-brand .brand-name { display: block; font-size: 64px; letter-spacing: 1px; }
  .front-brand .brand-tag { display: block; font-size: 22px; letter-spacing: 10px; margin-top: 6px; }

  /* Back side */
  .card-back { left: 610px; top: 290px; background: var(--paper); }
  .card-back svg.waves { position: absolute; inset: 0; }
  .back-brand {
    position: absolute; left: 36px; top: 92px;
    color: var(--ink); font-weight: 800; text-transform: uppercase; line-height: 1.1;
    display: flex; align-items: center; gap: 10px;
  }
  .back-brand .mark { width: 20px; height: 20px; background: var(--ink); flex: none; }
  .back-brand .brand-name { display: block; font-size: 32px; }
  .back-brand .brand-tag { display: block; font-size: 11px; letter-spacing: 6px; margin-top: 3px; }

  .contact {
    position: absolute; right: 28px; top: 74px;
    text-align: right; color: var(--paper);
  }
  .contact .person { color: var(--lime); font-weight: 800; font-size: 23px; text-transform: uppercase; letter-spacing: .5px; line-height: 1.15; }
  .contact .role { font-size: 12px; font-weight: 500; text-transform: uppercase; letter-spacing: 1px; margin: 2px 0 18px; }
  .contact ul { list-style: none; font-size: 13px; line-height: 22px; }
  .contact li { display: flex; justify-content: flex-end; align-items: center; gap: 8px; }
  .contact li svg { width: 12px; height: 12px; fill: var(--lime); flex: none; }
  .address {
    position: absolute; left: 40px; bottom: 20px;
    color: var(--paper); font-size: 14px; line-height: 20px;
  }
</style>
</head>
<body>

  <section class="card card-front" aria-label="Card front">
    <div class="front-brand">
      <span class="brand-name">Ridgeline</span>
      <span class="brand-tag">Design + Build</span>
    </div>
  </section>

  <section class="card card-back" aria-label="Card back">
    <svg class="waves" viewBox="0 0 560 320" width="560" height="320" aria-hidden="true">
      <path d="M0 214 C140 214 236 203 282 132 C320 62 360 24 560 10" fill="none" stroke="var(--lime)" stroke-width="8"/>
      <path d="M0 226 C140 226 238 214 286 141 C325 68 365 32 560 19" fill="none" stroke="var(--ink)" stroke-width="4"/>
      <path d="M0 236 C140 236 240 225 290 150 C330 78 370 40 560 28 L560 320 L0 320 Z" fill="var(--ink)"/>
    </svg>

    <div class="back-brand">
      <span class="mark"></span>
      <div>
        <span class="brand-name">Ridgeline</span>
        <span class="brand-tag">Design + Build</span>
      </div>
    </div>

    <div class="contact">
      <div class="person">Marcus Hale</div>
      <div class="role">Owner-CEO</div>
      <ul>
        <li>123 456 789
          <svg viewBox="0 0 12 12"><path d="M2 1h3l1 3-2 1a7 7 0 0 0 3 3l1-2 3 1v3a1 1 0 0 1-1 1A10 10 0 0 1 1 2a1 1 0 0 1 1-1z"/></svg></li>
        <li>123 456 789
          <svg viewBox="0 0 12 12"><path d="M3 0h6a1 1 0 0 1 1 1v10a1 1 0 0 1-1 1H3a1 1 0 0 1-1-1V1a1 1 0 0 1 1-1zm0 2v7h6V2z"/></svg></li>
        <li>info@ridgelinebuild.com
          <svg viewBox="0 0 12 12"><path d="M0 2h12v8H0zM1 3l5 4 5-4v-.2H1z"/></svg></li>
        <li>www.ridgelinebuild.com
          <svg viewBox="0 0 12 12"><circle cx="6" cy="6" r="6"/></svg></li>
      </ul>
    </div>

    <div class="address">Your address, City<br>State, Zip 1234</div>
  </section>

</body>
</html>
```